Theme and starter template for small business powerpoint deck

We are starting a technology consulting company and would like to have a powerpoint/google slide theme and initial template. We are more concerned with the theme/colors at this point. Initial template can be pretty simple. We would want a cover slide, agenda slide, some content slides including text content, image content, a combination of both, etc. A closing slide. we have included jpg files of our logo, let us know if you would prefer eps/vector. I assume you may want exact color data as well?

Target Market(s)

Technology and Customer Experience Leadership at companies with 25 or more employees

Industry/Entity Type

Technology Consulting

Font styles to use
Sans Serif

Colors
0054AA
0677BA
7BADD7
CADEEF
E8F1F8

Requirements
Must have
• I have attached JPG and EPS and vector files to project. I would like to stay with those colors but open to slight variation if recommended.

```html
<!DOCTYPE html>
<html lang="en">
<head>
<meta charset="utf-8">
<title>Vectaris Slide Theme</title>
<link href="https://fonts.googleapis.com/css2?family=Exo+2:wght@600;700;800&family=Mulish:wght@400;500;600&display=swap" rel="stylesheet">
<style>
:root{
  --blue:#0054aa;
  --blue-mid:#0677ba;
  --blue-soft:#7badd7;
  --blue-pale:#cadeef;
  --blue-mist:#e8f1f8;
  --ink:#111418;
  --text:#5a5f66;
  --page:#e7e7e9;
  --white:#ffffff;
}
*{margin:0;padding:0;box-sizing:border-box}
html,body{width:1046px;height:1200px;overflow:hidden}
body{background:var(--page);font-family:"Mulish",sans-serif;color:var(--text);position:relative}
.slide{position:absolute;width:460px;height:259px;background:var(--white);overflow:hidden}
.col-a{left:44px}.col-b{left:542px}
.row-1{top:34px}.row-2{top:325px}.row-3{top:616px}.row-4{top:908px}
.abs{position:absolute}
.photo{position:absolute}
.heading{position:absolute;left:23px;top:16px;font-family:"Exo 2",sans-serif;font-weight:700;font-size:13.5px;color:var(--ink);letter-spacing:.2px}
.heading em{font-style:normal;color:var(--blue)}
.heading-mark{position:absolute;left:0;top:17px;width:12px;height:15px;background:var(--blue)}
.footer-name{position:absolute;left:22px;top:229px;font-family:"Exo 2",sans-serif;font-weight:800;font-size:16px;color:var(--ink);letter-spacing:1px;line-height:20px}
.footer-name i{display:inline-block;width:8px;height:8px;background:var(--blue);margin-left:4px;vertical-align:1px}
.footer-bar{position:absolute;left:140px;right:0;top:231px;height:16px;background:var(--blue);clip-path:polygon(0 0,100% 0,100% 100%,10px 100%)}
.footer-bar span{position:absolute;right:25px;top:4px;font-size:4.6px;color:var(--white)}
.copy{font-size:4.8px;line-height:10.5px;text-align:justify}
.copy p+p{margin-top:7px}
/* cover */
.cover-bg{position:absolute;left:0;top:0;width:460px;height:242px;background:radial-gradient(circle at 30% 40%,#1a73c8 0%,#0b5cb3 45%,#0a4c9a 100%)}
.cover-name{position:absolute;left:41px;top:42px;font-family:"Exo 2",sans-serif;font-weight:800;font-size:24px;letter-spacing:2px;color:var(--white)}
.cover-name i{display:inline-block;width:13px;height:13px;background:var(--white);margin-left:6px;vertical-align:2px}
.cover-tag{position:absolute;left:38px;top:111px;width:184px;text-align:center;font-size:6.2px;line-height:12px;color:var(--white)}
.cover-rule{position:absolute;left:44px;top:158px;width:172px;height:1px;background:rgba(255,255,255,.35)}
.dots{position:absolute;display:flex;gap:4.6px}
.dot{width:18px;height:18px;border-radius:50%}
.cover-dots{left:75px;top:169px}.cover-dots .dot{background:var(--white)}
.cover-art{left:225px;top:19px;width:225px;height:194px;border-radius:6px;background:linear-gradient(135deg,rgba(90,110,230,.55),rgba(70,80,110,.45) 55%,rgba(190,30,40,.55))}
.cover-copy{position:absolute;left:0;right:0;top:246px;text-align:center;font-size:4.6px;color:var(--ink)}
.cover-copy b{color:var(--blue);font-weight:500}
/* toc */
.toc-panel{position:absolute;left:0;top:0;width:144px;height:205px;background:var(--blue-mid)}
.toc-title{position:absolute;left:19px;top:79px;font-family:"Exo 2",sans-serif;font-weight:700;font-size:14.5px;line-height:19px;color:var(--white)}
.toc-rule{position:absolute;left:19px;top:122px;width:83px;height:1px;background:var(--white)}
.toc-item{position:absolute;left:288px;height:16px;display:flex;align-items:center}
.toc-num{width:23px;height:16px;background:var(--blue);color:var(--white);font-family:"Exo 2",sans-serif;font-weight:700;font-size:7.5px;display:flex;align-items:center;padding-left:6px;clip-path:polygon(0 0,80% 0,100% 100%,0 100%)}
.toc-label{margin-left:9px;font-size:7.2px;color:#4d5157}
/* services */
.card{position:absolute;top:43px;width:132px;height:171px;background:var(--white);border-radius:5px;box-shadow:0 1px 6px rgba(0,0,0,.12);overflow:hidden;text-align:center}
.card .photo{position:relative;height:81px}
.card h3{font-family:"Exo 2",sans-serif;font-weight:700;font-size:8.3px;color:var(--blue);margin-top:8px}
.card p{font-size:4px;line-height:8.5px;margin:3px 10px 0}
.card p+p{margin-top:8px}
/* gallery */
.quote-box{position:absolute;background:var(--blue);color:var(--white)}
.quote-mark{font-family:"Exo 2",sans-serif;font-weight:800;font-size:20px;line-height:14px;height:14px}
/* thanks */
.thanks-art{position:absolute;left:150px;top:0;width:310px;height:259px;background:linear-gradient(90deg,rgba(232,241,248,0) 0%,#c7ced6 25%,#8e97a3 60%,#3a4a66 100%)}
.thanks-bg{position:absolute;inset:0;background:linear-gradient(90deg,#f4f7fa,#e6ecf2)}
.thanks-name{position:absolute;left:45px;top:100px;width:100px;text-align:center;font-family:"Exo 2",sans-serif;font-weight:700;font-size:10px;letter-spacing:1px;color:var(--ink)}
.thanks-name i{display:block;margin:0 auto 8px;width:38px;height:38px;background:var(--blue)}
.thanks-title{position:absolute;left:42px;top:162px;font-family:"Exo 2",sans-serif;font-weight:700;font-size:18px;color:var(--ink)}
.thanks-dots{left:41px;top:192px}.thanks-dots .dot{background:var(--blue)}
</style>
</head>
<body>

<!-- Cover -->
<section class="slide col-a row-1">
  <div class="cover-bg"></div>
  <div class="cover-name">VECTARIS<i></i></div>
  <p class="cover-tag">I must explain to you how all this mistaken idea of denouncing pleasure and praising pain was born and I will give you a complete account of the system</p>
  <div class="cover-rule"></div>
  <div class="dots cover-dots"><span class="dot"></span><span class="dot"></span><span class="dot"></span><span class="dot"></span><span class="dot"></span></div>
  <div class="photo cover-art" role="img" aria-label="Abstract artwork of a world map and network lines in blue, grey and red"></div>
  <p class="cover-copy">(C) Copyright 2024 <b>Vectaris</b> | All Rights Reserved</p>
</section>

<!-- What we do -->
<section class="slide col-b row-1">
  <div class="heading-mark"></div>
  <h2 class="heading">WHAT <em>WE DO</em></h2>
  <div class="abs copy" style="left:23px;top:48px;width:196px">
    <p>At vero eos et accusamus et iusto odio dignissimos ducimus qui blanditiis praesentium voluptatum deleniti atque corrupti quos dolores et quas molestias excepturi sint occaecati cupiditate non provident, similique sunt in culpa qui officia deserunt mollitia animi, id est laborum et dolorum fuga. Et harum quidem rerum facilis est et expedita distinctio. Nam libero tempore, cum soluta nobis est eligendi optio cumque nihil impedit quo minus id quod maxime placeat facere possimus, omnis voluptas assumenda est, omnis dolor repellendus.</p>
    <p>Nam libero tempore, cum soluta nobis est eligendi optio cumque nihil impedit quo minus id quod maxime placeat facere possimus, omnis voluptas assumenda est, omnis dolor repellendus.</p>
    <p>Temporibus autem quibusdam et aut officiis debitis aut rerum necessitatibus saepe eveniet ut et voluptates repudiandae sint et molestiae non recusandae. Itaque earum rerum hic tenetur a sapiente delectus, ut aut reiciendis voluptatibus maiores alias consequatur aut perferendis doloribus asperiores repellat.</p>
  </div>
  <div class="abs copy" style="left:240px;top:48px;width:196px">
    <p>At vero eos et accusamus et iusto odio dignissimos ducimus qui blanditiis praesentium voluptatum deleniti atque corrupti quos dolores et quas molestias excepturi sint occaecati cupiditate non provident, similique sunt in culpa qui officia deserunt mollitia animi, id est laborum et dolorum fuga. Et harum quidem rerum facilis est et expedita distinctio. Nam libero tempore, cum soluta nobis est eligendi optio cumque nihil impedit quo minus id quod maxime placeat facere possimus, omnis voluptas assumenda est, omnis dolor repellendus.</p>
    <p>Nam libero tempore, cum soluta nobis est eligendi optio cumque nihil impedit quo minus id quod maxime placeat facere possimus, omnis voluptas assumenda est, omnis dolor repellendus.</p>
    <p>Temporibus autem quibusdam et aut officiis debitis aut rerum necessitatibus saepe eveniet ut et voluptates repudiandae sint et molestiae non recusandae. Itaque earum rerum hic tenetur a sapiente delectus, ut aut reiciendis voluptatibus maiores alias consequatur aut perferendis doloribus asperiores repellat.</p>
  </div>
  <div class="footer-name">VECTARIS<i></i></div>
  <div class="footer-bar"><span>(C) Copyright 2024 Vectaris | All Rights Reserved</span></div>
</section>

<!-- Table of contents -->
<section class="slide col-a row-2">
  <div class="toc-panel"></div>
  <h2 class="toc-title">TABLE<br>OF CONTENTS</h2>
  <div class="toc-rule"></div>
  <div class="photo" style="left:144px;top:0;width:144px;height:205px;background:linear-gradient(160deg,#b9bcc0,#7c8088 60%,#4d5560)" role="img" aria-label="Photo of two colleagues talking over a tablet in an office"></div>
  <div class="toc-item" style="top:29px"><span class="toc-num">01</span><span class="toc-label">Introduction</span></div>
  <div class="toc-item" style="top:58px"><span class="toc-num">02</span><span class="toc-label">Table Of Contents (Agenda)</span></div>
  <div class="toc-item" style="top:88px"><span class="toc-num">03</span><span class="toc-label">Who We Are</span></div>
  <div class="toc-item" style="top:117px"><span class="toc-num">04</span><span class="toc-label">Our History</span></div>
  <div class="toc-item" style="top:147px"><span class="toc-num">05</span><span class="toc-label">What we do</span></div>
  <div class="toc-item" style="top:177px"><span class="toc-num">06</span><span class="toc-label">Our Services &amp; Work</span></div>
  <div class="footer-name">VECTARIS<i></i></div>
  <div class="footer-bar"><span>(C) Copyright 2024 Vectaris | All Rights Reserved</span></div>
</section>

<!-- Services -->
<section class="slide col-b row-2">
  <div class="heading-mark"></div>
  <h2 class="heading">OUR <em>SERVICES &amp; WORK</em></h2>
  <article class="card" style="left:23px">
    <div class="photo" style="background:linear-gradient(160deg,#e6e8ea,#9ea3a9)" role="img" aria-label="Photo of hands reviewing documents at a laptop"></div>
    <h3>SERVICE ONE</h3>
    <p>At vero eos et accusamus et iusto odio dignissimos ducimus qui blanditiis praesentium voluptatum deleniti atque corrupti quos dolores et quas molestias excepturi sint occaecati cupiditate</p>
    <p>Non provident, similique sunt in culpa qui officia deserunt mollitia animi, id est laborum.</p>
  </article>
  <article class="card" style="left:165px">
    <div class="photo" style="background:linear-gradient(160deg,#d9d4cf,#8b8580)" role="img" aria-label="Photo of a team working together at a table"></div>
    <h3>SERVICE TWO</h3>
    <p>At vero eos et accusamus et iusto odio dignissimos ducimus qui blanditiis praesentium voluptatum deleniti atque corrupti quos dolores et quas molestias excepturi sint occaecati cupiditate</p>
    <p>Non provident, similique sunt in culpa qui officia deserunt mollitia animi, id est laborum.</p>
  </article>
  <article class="card" style="left:305px">
    <div class="photo" style="background:linear-gradient(160deg,#cdd3d9,#5e6672)" role="img" aria-label="Photo of a business meeting around a conference table"></div>
    <h3>SERVICE THREE</h3>
    <p>At vero eos et accusamus et iusto odio dignissimos ducimus qui blanditiis praesentium voluptatum deleniti atque corrupti quos dolores et quas molestias excepturi sint occaecati cupiditate</p>
    <p>Non provident, similique sunt in culpa qui officia deserunt mollitia animi, id est laborum.</p>
  </article>
  <div class="footer-name">VECTARIS<i></i></div>
  <div class="footer-bar"><span>(C) Copyright 2024 Vectaris | All Rights Reserved</span></div>
</section>

<!-- About -->
<section class="slide col-a row-3">
  <div class="heading-mark"></div>
  <h2 class="heading">ABOUT <em>US</em></h2>
  <div class="abs copy" style="left:23px;top:42px;width:188px">
    <p>At vero eos et accusamus et iusto odio dignissimos ducimus qui blanditiis praesentium voluptatum deleniti atque corrupti quos dolores et quas molestias excepturi sint occaecati cupiditate non provident, similique sunt in culpa qui officia deserunt mollitia animi, id est laborum et dolorum fuga. Et harum quidem rerum facilis est et expedita distinctio. Nam libero tempore, cum soluta nobis est eligendi optio cumque nihil impedit quo minus id quod maxime placeat facere possimus, omnis voluptas assumenda est, omnis dolor repellendus.</p>
    <p>Nam libero tempore, cum soluta nobis est eligendi optio cumque nihil impedit quo minus id quod maxime placeat facere possimus, omnis voluptas assumenda est, omnis dolor repellendus.</p>
    <p>Temporibus autem quibusdam et aut officiis debitis aut rerum necessitatibus saepe eveniet ut et voluptates repudiandae sint et molestiae non recusandae. Itaque earum rerum hic tenetur a sapiente delectus, ut aut reiciendis voluptatibus maiores alias consequatur aut perferendis doloribus asperiores repellat.</p>
  </div>
  <div class="photo" style="left:231px;top:37px;width:204px;height:172px;background:linear-gradient(150deg,#9fb6c8,#4e6478 55%,#1f2c3c);box-shadow:0 2px 8px rgba(0,0,0,.2)" role="img" aria-label="Photo of a presenter leading a meeting in a glass-walled office"></div>
  <div class="footer-name">VECTARIS<i></i></div>
  <div class="footer-bar"><span>(C) Copyright 2024 Vectaris | All Rights Reserved</span></div>
</section>

<!-- Gallery -->
<section class="slide col-b row-3">
  <div class="heading-mark"></div>
  <h2 class="heading">OUR <em>PROJECT GALLERY</em></h2>
  <div class="photo" style="left:22px;top:43px;width:176px;height:84px;background:linear-gradient(150deg,#e4e2df,#8a817a 60%,#3a3d48)" role="img" aria-label="Photo of two colleagues smiling over a laptop"></div>
  <div class="quote-box" style="left:207px;top:43px;width:127px;height:84px;padding:12px 11px">
    <div class="quote-mark">&ldquo;</div>
    <p style="font-size:5.3px;line-height:10.8px;margin-top:3px">At vero eos et accusamus et iusto odio dignissimos ducimus qui blanditiis praesentium voluptatum deleniti atque corrupti</p>
  </div>
  <div class="photo" style="left:340px;top:43px;width:96px;height:174px;background:linear-gradient(160deg,#d6d3cc,#8e8378 55%,#3b3a44)" role="img" aria-label="Photo of two colleagues reviewing a tablet"></div>
  <div class="photo" style="left:22px;top:134px;width:176px;height:83px;background:linear-gradient(135deg,#0c2340,#1b6aa5 55%,#0a1a30)" role="img" aria-label="Photo of hands on a laptop with digital interface graphics"></div>
  <div class="photo" style="left:207px;top:134px;width:61px;height:83px;background:linear-gradient(160deg,#cfd4d9,#6d7480)" role="img" aria-label="Photo of two professionals with a tablet"></div>
  <div class="photo" style="left:273px;top:134px;width:61px;height:83px;background:linear-gradient(135deg,#1b2a6b,#6a3fa0 50%,#c04a7a)" role="img" aria-label="Photo of a laptop with colourful data light streams"></div>
  <div class="footer-name">VECTARIS<i></i></div>
  <div class="footer-bar"><span>(C) Copyright 2024 Vectaris | All Rights Reserved</span></div>
</section>

<!-- History -->
<section class="slide col-a row-4">
  <div class="heading-mark"></div>
  <h2 class="heading">OUR <em>HISTORY</em></h2>
  <div class="photo" style="left:23px;top:45px;width:132px;height:172px;background:linear-gradient(170deg,#3a3a40,#1f1c22 55%,#5a3a25)" role="img" aria-label="Photo of a hand touching glowing network icons"></div>
  <div class="photo" style="left:167px;top:45px;width:115px;height:101px;background:linear-gradient(160deg,#d6d2cb,#8d8479 60%,#4a4541)" role="img" aria-label="Photo of a team working at laptops in an office"></div>
  <div class="abs copy" style="left:295px;top:42px;width:140px">
    <p>At vero eos et accusamus et iusto odio dignissimos ducimus qui blanditiis praesentium voluptatum deleniti atque corrupti quos dolores et quas molestias excepturi sint occaecati cupiditate non provident, similique sunt in culpa qui officia deserunt mollitia animi, id est laborum et dolorum fuga.</p>
    <p>Et harum quidem rerum facilis est et expedita distinctio. Nam libero tempore, cum soluta nobis est eligendi optio cumque nihil impedit quo minus id quod maxime placeat facere possimus, omnis voluptas</p>
  </div>
  <div class="quote-box" style="left:167px;top:159px;width:268px;height:58px;padding:9px 17px">
    <div class="quote-mark">&ldquo;</div>
    <p style="font-size:4.4px;line-height:8.3px;margin-top:3px">At vero eos et accusamus et iusto odio dignissimos ducimus qui blanditiis praesentium voluptatum deleniti atque corrupti quos dolores et quas molestias excepturi sint occaecati cupiditate non provident, similique sunt in culpa qui officia deserunt mollitia animi.</p>
  </div>
  <div class="footer-name">VECTARIS<i></i></div>
  <div class="footer-bar"><span>(C) Copyright 2024 Vectaris | All Rights Reserved</span></div>
</section>

<!-- Thank you -->
<section class="slide col-b row-4">
  <div class="thanks-bg"></div>
  <div class="thanks-art" role="img" aria-label="Photo of two colleagues smiling while looking at a tablet"></div>
  <div class="thanks-name"><i></i>VECTARIS</div>
  <h2 class="thanks-title">THANK YOU</h2>
  <div class="dots thanks-dots"><span class="dot"></span><span class="dot"></span><span class="dot"></span><span class="dot"></span><span class="dot"></span></div>
</section>

</body>
</html>
```